Stylish Business Cards Wanted

- DOUBLE SIDED Design Required -

High end, edgy cards for a corporate and personal stylist. Must include logo,
Name: Belinda Harwick
Title: Director and Stylist
telephone : +61 8 7142 5809
email: belinda@theloombriefing.example
website: theloombriefing.example
Tag: Corporate Workwear & Uniform Specialist | Personal Stylist
Would like nice icons for telephone, email, website

Target Market(s)

Businesses wanting stylish uniforms, people wanting stylish wardrobes

Industry/Entity Type

Corporate Workwear Stylist

Contact Information for Business Card

I would like black, white and gold foiling incorporated in the design - possibly a touch of the other colours on my branding guide attached Name: Belinda Harwick Title: Director and Stylist telephone : +61 8 7142 5809 email: belinda@theloombriefing.example website: theloombriefing.example Tag: Corporate Workwear & Uniform Specialist | Personal Stylist Would like nice icons for telephone, email, website

Font styles to use
Other font styles liked:
• Raleway

Colors

Designer to choose colors to be used in the design.

Requirements
Must have
• Gold foil accents

```html
<!DOCTYPE html>
<html lang="en">
<head>
<meta charset="utf-8">
<title>The Loom Briefing — Business Cards</title>
<link rel="stylesheet" href="https://fonts.googleapis.com/css2?family=Arimo:wght@400;700&family=Norican&display=swap">
<style>
  :root {
    --backdrop: #a9a9a9;
    --card-black: #231f20;
    --card-white: #ffffff;
    --gold: #e2b34f;
    --ink: #1a1718;
    --pale: #dfe1df;
    --ghost: #efefef;
  }
  * { box-sizing: border-box; margin: 0; padding: 0; }
  html, body { width: 1200px; height: 900px; overflow: hidden; }
  body {
    background: var(--backdrop);
    font-family: "Arimo", Arial, sans-serif;
    position: relative;
  }
  .card {
    position: absolute;
    width: 600px;
    height: 367px;
    border-radius: 28px;
    overflow: hidden;
    box-shadow: 0 6px 14px rgba(0,0,0,.28);
  }
  .brand {
    position: absolute;
    font-family: "Arimo", Arial, sans-serif;
    font-weight: 700;
    line-height: 1.05;
  }

  /* Front */
  .card--front { left: 150px; top: 70px; background: var(--card-black); }
  .card--front .brand {
    left: 0; right: 0; top: 100px;
    text-align: center;
    font-size: 50px;
    color: var(--pale);
    letter-spacing: 1px;
    white-space: nowrap;
  }
  .tag-band {
    position: absolute;
    left: 70px; right: 28px; bottom: 40px;
    height: 34px;
    background: var(--gold);
    display: flex; align-items: center; justify-content: center;
    font-size: 15px;
    color: var(--ink);
    white-space: nowrap;
  }
  .tag-band .dot { margin: 0 10px; font-weight: 700; }

  /* Back */
  .card--back { left: 450px; top: 470px; background: var(--card-white); }
  .card--back .brand--ghost {
    right: 30px; top: 60px;
    text-align: right;
    font-size: 48px;
    color: var(--ghost);
  }
  .card--back .brand--main {
    left: 60px; top: 52px;
    font-size: 34px;
    color: var(--ink);
  }
  .brand span { display: block; white-space: nowrap; }
  .person { position: absolute; left: 70px; top: 158px; }
  .person__name {
    font-family: "Norican", cursive;
    font-size: 36px;
    color: var(--gold);
    line-height: 1.1;
  }
  .person__title { font-size: 17px; color: var(--ink); margin-top: 2px; }
  .contacts { list-style: none; margin-top: 16px; }
  .contacts li {
    display: flex; align-items: center; gap: 10px;
    font-size: 16px; color: var(--ink);
    margin-bottom: 7px;
    white-space: nowrap;
  }
  .contacts svg { width: 18px; height: 18px; flex: none; }
</style>
</head>
<body>

<section class="card card--front" aria-label="Card front">
  <div class="brand">The Loom Briefing</div>
  <div class="tag-band">
    <span>Corporate Workwear &amp; Uniform Specialist</span>
    <span class="dot">•</span>
    <span>Personal Stylist</span>
  </div>
</section>

<section class="card card--back" aria-label="Card back">
  <div class="brand brand--ghost" aria-hidden="true"><span>The Loom</span><span>Briefing</span></div>
  <div class="brand brand--main"><span>The Loom</span><span>Briefing</span></div>
  <div class="person">
    <p class="person__name">Belinda Harwick</p>
    <p class="person__title">Director and Stylist</p>
    <ul class="contacts">
      <li>
        <svg viewBox="0 0 24 24" aria-hidden="true"><path fill="var(--gold)" d="M6.6 10.8a15.1 15.1 0 0 0 6.6 6.6l2.2-2.2a1 1 0 0 1 1-.25 11.4 11.4 0 0 0 3.6.57 1 1 0 0 1 1 1V20a1 1 0 0 1-1 1A17 17 0 0 1 3 4a1 1 0 0 1 1-1h3.5a1 1 0 0 1 1 1c0 1.250.2 2.460.57 3.6a1 1 0 0 1-.25 1z"/></svg>
        <span>+61 8 7142 5809</span>
      </li>
      <li>
        <svg viewBox="0 0 24 24" aria-hidden="true"><rect x="2" y="5" width="20" height="14" rx="1" fill="var(--gold)"/><path d="M2.5 6l9.5 7 9.5-7" fill="none" stroke="#fff" stroke-width="1.6"/></svg>
        <span>belinda@theloombriefing.example</span>
      </li>
      <li>
        <svg viewBox="0 0 24 24" aria-hidden="true"><g fill="none" stroke="var(--gold)" stroke-width="1.8"><circle cx="12" cy="12" r="9"/><ellipse cx="12" cy="12" rx="4" ry="9"/><path d="M3 12h18M5 7h14M5 17h14"/></g></svg>
        <span>theloombriefing.example</span>
      </li>
    </ul>
  </div>
</section>

</body>
</html>
```